Heron Haulage needs Bussiness cards!

Our new trucking company needs business cards!
We need the same design with two different names and emails, everything else it's the same.
I have included our original logo so we can use it for the design.
Note: the logo to be used is the o e with the buffalo on the right side, next to the letters H and H.

Target Market(s)

Trucking, refrigerated transportation, freight

Industry/Entity Type

Business

Contact Information for Business Card

Card #1:
Marcus Whitfield
marcuswhitfield@heronhaulage.example
1-855-317-6094
(555)238-7160
4117 W. Larkin Ave.
Marlow Springs, TX 78590
www.heronhaulage.example

Card#2:
Rosalba Quintero
rosalba@heronhaulage.example
1-855-317-6094
(555)238-7160
4117 W. Larkin Ave.
Marlow Springs, TX 78590
www.heronhaulage.example

Font styles to use
Sans Serif

Colors
0655a3
ec1f27
ffffff

Requirements
Must have
• our logo
Nice to have
• roads on background,

```html
<!DOCTYPE html>
<html lang="en">
<head>
<meta charset="utf-8">
<title>Heron Haulage — Business Cards</title>
<link rel="stylesheet" href="https://fonts.googleapis.com/css2?family=Montserrat:wght@400;500;800&display=swap">
<style>
  :root {
    --navy: #0b2d5c;
    --red: #c8102e;
    --white: #ffffff;
    --sky: #2f8fd8;
    --backdrop: #2b2b2d;
  }
  * { margin: 0; padding: 0; box-sizing: border-box; }
  html, body { width: 1200px; height: 900px; overflow: hidden; }
  body {
    background: var(--backdrop);
    font-family: "Montserrat", Arial, sans-serif;
    position: relative;
  }
  .card {
    position: absolute;
    left: 280px;
    width: 640px;
    height: 366px;
    border-radius: 22px;
    overflow: hidden;
  }
  .card--front { top: 60px; background: var(--navy); }
  .card--details { top: 474px; background: var(--white); }

  .brand-name {
    font-weight: 800;
    color: var(--white);
    letter-spacing: -0.5px;
    line-height: 1;
    white-space: nowrap;
  }
  .card--front .brand {
    position: absolute;
    left: 0; right: 0; top: 132px;
    text-align: center;
  }
  .card--front .brand-name { font-size: 52px; }
  .card--front .brand-url {
    margin-top: 22px;
    color: var(--white);
    font-size: 17px;
    font-weight: 500;
    letter-spacing: 0.3px;
  }

  .details-shape { position: absolute; inset: 0; }
  .card--details .brand {
    position: absolute;
    left: 34px; top: 58px;
    display: flex; align-items: center; gap: 10px;
  }
  .card--details .brand-name { color: var(--red); font-size: 34px; }
  .brand-dot {
    width: 14px; height: 14px; border-radius: 50%;
    background: var(--navy);
  }

  .contact {
    position: absolute;
    left: 40px; top: 210px;
    color: var(--white);
  }
  .contact-name {
    color: var(--red);
    font-weight: 800;
    font-size: 19px;
    letter-spacing: 0.6px;
    text-transform: uppercase;
    margin-bottom: 6px;
    white-space: nowrap;
  }
  .contact-line {
    font-size: 13.5px;
    line-height: 18px;
    display: flex; align-items: center; gap: 8px;
    white-space: nowrap;
  }
  .contact-line--plain { padding-left: 20px; }
  .contact-icon { width: 12px; height: 12px; flex: none; }
</style>
</head>
<body>

  <section class="card card--front">
    <div class="brand">
      <div class="brand-name">Heron Haulage</div>
      <div class="brand-url">www.heronhaulage.example</div>
    </div>
  </section>

  <section class="card card--details">
    <svg class="details-shape" viewBox="0 0 640 366" preserveAspectRatio="none">
      <polygon points="0,196 640,30 640,44 0,210" fill="var(--red)"/>
      <polygon points="0,216 640,50 640,366 0,366" fill="var(--navy)"/>
      <polygon points="220,170 640,58 640,64 220,176" fill="var(--sky)" opacity="0.7"/>
    </svg>

    <div class="brand">
      <span class="brand-name">Heron Haulage</span>
      <span class="brand-dot"></span>
    </div>

    <div class="contact">
      <div class="contact-name">Marcus Whitfield</div>
      <div class="contact-line contact-line--plain">4117 W. Larkin Ave.</div>
      <div class="contact-line contact-line--plain">Marlow Springs, TX 78590</div>
      <div class="contact-line">
        <svg class="contact-icon" viewBox="0 0 12 12"><path d="M2.5 1 L4.5 1 L5.2 3.6 L4 4.6 Q5 7 7.4 8 L8.4 6.8 L11 7.5 L11 9.5 Q10.5 11 9 11 Q1 10 1 3 Q1 1.5 2.5 1 Z" fill="var(--red)"/></svg>
        1-855-317-6094
      </div>
      <div class="contact-line">
        <svg class="contact-icon" viewBox="0 0 12 12"><rect x="3" y="0.5" width="6" height="11" rx="1.2" fill="none" stroke="var(--red)" stroke-width="1.3"/><circle cx="6" cy="9.4" r="0.8" fill="var(--red)"/></svg>
        (555)238-7160
      </div>
      <div class="contact-line">
        <svg class="contact-icon" viewBox="0 0 12 12"><circle cx="6" cy="6" r="5" fill="none" stroke="var(--red)" stroke-width="1.2"/><ellipse cx="6" cy="6" rx="2.2" ry="5" fill="none" stroke="var(--red)" stroke-width="1"/><line x1="1" y1="6" x2="11" y2="6" stroke="var(--red)" stroke-width="1"/></svg>
        www.heronhaulage.example
      </div>
      <div class="contact-line">
        <svg class="contact-icon" viewBox="0 0 12 12"><rect x="0.8" y="2.2" width="10.4" height="7.6" rx="1" fill="none" stroke="var(--red)" stroke-width="1.2"/><polyline points="1,2.8 6,6.8 11,2.8" fill="none" stroke="var(--red)" stroke-width="1.2"/></svg>
        marcuswhitfield@heronhaulage.example
      </div>
    </div>
  </section>

</body>
</html>
```